Corporate Business Card

Very professional, Modern, Not to busy, include phone address email, website
(253) 617-4930, 18761 52nd Avenue S, Renmore, OR 98047, martin@plumlinegroup.com, varkoworks.com

Target Market(s)

Manufacturing

Industry/Entity Type

Aero, machining, manufacturing, Off road racing

Contact Information for Business Card

Phone, address email, website

```html
<!DOCTYPE html>
<html lang="en">
<head>
<meta charset="utf-8">
<title>Varko Industries – Business Card</title>
<link href="https://fonts.googleapis.com/css2?family=Montserrat:wght@400;500;700&display=swap" rel="stylesheet">
<style>
  :root {
    --backdrop: #6d6d6d;
    --card: #ffffff;
    --navy: #17366e;
    --red: #d4222b;
    --ink: #1c1c1c;
  }
  * { box-sizing: border-box; margin: 0; padding: 0; }
  html, body {
    width: 1200px; height: 801px; overflow: hidden;
    background: var(--backdrop);
    font-family: "Montserrat", Arial, sans-serif;
  }
  .sheet {
    position: relative; width: 1200px; height: 801px;
    display: flex; align-items: center; justify-content: center; gap: 40px;
  }
  .card {
    position: relative; width: 560px; height: 320px;
    background: var(--card);
    border-bottom: 3px solid var(--red);
    overflow: hidden;
  }
  .band { position: absolute; }
  .band--red { background: var(--red); }
  .band--navy { background: var(--navy); }

  /* info side */
  .info .band--red { top: 0; left: 360px; width: 150px; height: 12px; }
  .info .band--navy { bottom: 0; left: 36px; width: 120px; height: 12px; }
  .brand {
    position: absolute; color: var(--navy); font-weight: 700;
    letter-spacing: 0.5px; white-space: nowrap;
  }
  .info .brand { left: 38px; top: 132px; font-size: 25px; }
  .brand-rule { position: absolute; height: 2px; background: var(--navy); }
  .info .brand-rule { left: 38px; top: 176px; width: 190px; }
  .divider {
    position: absolute; left: 290px; top: 56px; width: 2px; height: 210px;
    background: var(--red);
  }
  .details { position: absolute; left: 314px; top: 58px; color: var(--ink); }
  .details .name {
    color: var(--red); font-weight: 700; font-size: 20px;
    letter-spacing: 0.5px; text-transform: uppercase;
  }
  .details .role { font-size: 13px; margin-top: 2px; }
  .details .address { font-size: 13px; line-height: 1.45; margin-top: 14px; }
  .contact-list { list-style: none; margin-top: 12px; font-size: 13px; }
  .contact-list li { display: flex; align-items: center; gap: 7px; line-height: 1.75; }
  .contact-list svg { width: 13px; height: 13px; flex: none; }

  /* logo side */
  .cover .band--red { right: 0; top: 32px; width: 12px; height: 140px; }
  .cover .band--navy { left: 0; top: 180px; width: 12px; height: 110px; }
  .cover .brand { left: 0; right: 0; top: 118px; text-align: center; font-size: 44px; }
  .cover .brand-rule { left: 70px; top: 192px; width: 230px; }
</style>
</head>
<body>
<main class="sheet">

  <section class="card info">
    <span class="band band--red"></span>
    <span class="band band--navy"></span>

    <div class="brand">Varko Industries</div>
    <span class="brand-rule"></span>

    <span class="divider"></span>

    <div class="details">
      <p class="name">Daniel Reyes</p>
      <p class="role">Owner/CEO</p>
      <p class="address">Suite 410, 18761 52nd<br>Avenue S, Renmore, OR 98047</p>
      <ul class="contact-list">
        <li>
          <svg viewBox="0 0 16 16" aria-hidden="true"><circle cx="8" cy="8" r="8" fill="var(--red)"/><path d="M5 4.5l1.6-.5 1 2.2-1 .8a5 5 0 0 0 2.4 2.4l.8-1 2.2 1-.5 1.6c-3.5.3-6.8-3-6.5-6.5z" fill="#fff"/></svg>
          (253) 617-4930
        </li>
        <li>
          <svg viewBox="0 0 16 16" aria-hidden="true"><circle cx="8" cy="8" r="8" fill="var(--red)"/><rect x="4" y="5" width="8" height="6" fill="#fff"/><path d="M4 5l4 3.3L12 5" stroke="var(--red)" stroke-width="1" fill="none"/></svg>
          martin@plumlinegroup.com
        </li>
        <li>
          <svg viewBox="0 0 16 16" aria-hidden="true"><circle cx="8" cy="8" r="8" fill="var(--red)"/><circle cx="8" cy="8" r="4.2" fill="none" stroke="#fff" stroke-width="1.1"/><path d="M3.8 8h8.4M8 3.8c-2 2.4-2 6 0 8.4M8 3.8c2 2.4 2 6 0 8.4" stroke="#fff" stroke-width="0.9" fill="none"/></svg>
          www.varkoworks.com
        </li>
      </ul>
    </div>
  </section>

  <section class="card cover">
    <span class="band band--red"></span>
    <span class="band band--navy"></span>
    <div class="brand">Varko Industries</div>
    <span class="brand-rule"></span>
  </section>

</main>
</body>
</html>
```